Upscale business cards needed for Board of Directors

We need professional business cards created for members of our family business Board of Directors. We would like these relatively simple and straightforward, but also with a unique element to set them apart. Probably stick with neutral and simple colors - white, grey etc. We need space for the traditional elements, including name, title, address, email/phone number. And we will be creating several from this template so it needs to be template that is easy to switch information in and out of.
Business
See description

```html
<!DOCTYPE html>
<html lang="en">
<head>
<meta charset="utf-8">
<title>Corvane Holdings — Business Cards</title>
<link href="https://fonts.googleapis.com/css2?family=Lato:wght@400;700;900&display=swap" rel="stylesheet">
<style>
  :root {
    --backdrop: #3b3b3b;
    --card-white: #ffffff;
    --ink: #0a0a0a;
    --gold: #b09d74;
    --text-light: #ffffff;
  }
  * { margin: 0; padding: 0; box-sizing: border-box; }
  html, body { width: 1200px; height: 900px; overflow: hidden; }
  body {
    background: var(--backdrop);
    font-family: "Lato", sans-serif;
    position: relative;
  }
  .card {
    position: absolute;
    left: 285px;
    width: 630px;
    height: 360px;
    background: var(--card-white);
    overflow: hidden;
  }
  .card-front { top: 60px; }
  .card-back { top: 480px; }

  .front-brand {
    position: absolute;
    top: 100px;
    left: 0; right: 0;
    text-align: center;
    font-weight: 900;
    color: var(--ink);
    line-height: 1.05;
  }
  .front-brand .brand-main,
  .front-brand .brand-sub { display: block; font-size: 58px; letter-spacing: 1px; }
  .front-url {
    position: absolute;
    top: 272px;
    left: 0; right: 0;
    text-align: center;
    font-size: 16px;
    letter-spacing: 2px;
    color: var(--ink);
  }

  .back-shapes { position: absolute; inset: 0; }
  .back-brand {
    position: absolute;
    top: 30px;
    left: 32px;
    font-weight: 900;
    color: var(--ink);
    line-height: 1.05;
    font-size: 34px;
    letter-spacing: 1px;
  }
  .back-brand span { display: block; }
  .person {
    position: absolute;
    top: 112px;
    left: 420px;
  }
  .person-name { font-size: 26px; color: var(--gold); font-weight: 400; }
  .person-title { font-size: 14px; color: var(--ink); margin-top: 1px; }
  .address {
    position: absolute;
    top: 238px;
    left: 32px;
    color: var(--text-light);
    font-size: 15px;
    font-style: normal;
    line-height: 1.35;
  }
  .contact-list {
    position: absolute;
    top: 252px;
    left: 330px;
    list-style: none;
    color: var(--text-light);
    font-size: 18px;
    line-height: 24px;
  }
  .contact-list li { display: flex; align-items: center; gap: 12px; }
  .contact-list svg { width: 16px; height: 16px; fill: var(--gold); flex: none; }
</style>
</head>
<body>

  <section class="card card-front" aria-label="Card front">
    <h1 class="front-brand">
      <span class="brand-main">CORVANE</span>
      <span class="brand-sub">HOLDINGS</span>
    </h1>
    <p class="front-url">www.corvane.com</p>
  </section>

  <section class="card card-back" aria-label="Card back">
    <svg class="back-shapes" viewBox="0 0 630 360" width="630" height="360" aria-hidden="true">
      <path fill="var(--gold)" d="M0,136 C150,90 300,128 425,184 C505,220 575,204 630,196 L630,360 L0,360 Z"/>
      <path fill="var(--ink)" stroke="var(--card-white)" stroke-width="3"
            d="M0,154 C150,116 300,150 420,208 C500,246 570,230 630,224 L630,362 L-2,362 Z"/>
    </svg>

    <div class="back-brand"><span>CORVANE</span><span>HOLDINGS</span></div>

    <div class="person">
      <p class="person-name">Daniel Marsh</p>
      <p class="person-title">Director</p>
    </div>

    <address class="address">
      1450 Elm Ridge<br>Marlow TX 78100
    </address>

    <ul class="contact-list">
      <li>
        <svg viewBox="0 0 16 16"><path d="M3.5 1 L6 1 L7 4.5 L5.3 5.6 C6 7.6 8.4 10 10.4 10.7 L11.5 9 L15 10 L15 12.5 C15 13.9 13.9 15 12.5 15 C6.7 15 1 9.3 1 3.5 C1 2.1 2.1 1 3.5 1 Z"/></svg>
        512 004 2210
      </li>
      <li>
        <svg viewBox="0 0 16 16"><path d="M4 1 H12 V5 H4 Z M1 6 H15 V12 H12 V15 H4 V12 H1 Z M5 10 V14 H11 V10 Z"/></svg>
        512 004 2211
      </li>
      <li>
        <svg viewBox="0 0 16 16"><path d="M1 3 H15 V4 L8 9 L1 4 Z M1 5.5 L8 10.5 L15 5.5 V13 H1 Z"/></svg>
        info@corvane.com
      </li>
      <li>
        <svg viewBox="0 0 16 16"><circle cx="8" cy="8" r="7" fill="none" stroke="var(--gold)" stroke-width="1.5"/><ellipse cx="8" cy="8" rx="3" ry="7" fill="none" stroke="var(--gold)" stroke-width="1.2"/><path d="M1 8 H15" stroke="var(--gold)" stroke-width="1.2"/></svg>
        www.corvane.com
      </li>
    </ul>
  </section>

</body>
</html>
```